Upstart Retirement Planning Firm needs help with business card design

Harborview Nest Advisors, LLC is looking for help with business card design. We give advice on investments, insurance, and other financial matters related to retirement. There are some required disclosures that we will provide but mostly we are looking for a professional, classy business card that reflects the theme we have chosen. We have a logo that is attached but we would like to add a phrase; "Turning Your Earned Income Into Retirement Income"

Doubled sided only so that we can add the required disclosures (needed for our industry) on the back of the card. We will provide the exact words for this in 1-2 days.

Target Market(s)

Retirees and Pre-retirees. Professionals 50+ years old

Industry/Entity Type

Financial Planning

Contact Information for Business Card

We currently have two people who will need separate cards so we'd like to have a template so that we can add names for new cards in the future.

For the first run, please show the following information.

Gregor Pelham, MBA, ChFC®, CLU®
Financial Advisor, Registered Representative
gpelham@harborviewnest.example
Phone: (555) 318-2946
Toll Free Fax: (800) 555-0193

Address is
2187 Meadowlark Ridge Rd.
Suite K418
Virginia Beach, VA 23999

Colors
3277b5

Requirements
Must have
• Logo, contact info, small phase to describe business (in description), required legal disclosures on back of the card as follows (in small font)
• Gregor Pelham is a registered representative of and offers securities through Brightmoor Capital Brokerage Corporation, Member FNQX. Brightmoor Capital Brokerage Corporation is a member of the Brightmoor Capital Alliance which is the marketing name for Brightmoor Holding Corporation and its affiliates.
Nice to have
• Rounded edges, raised letters
Should not have
• any colors that aren't in the logo (other than black for font)

```html
<!DOCTYPE html>
<html lang="en">
<head>
<meta charset="utf-8">
<title>Harborview Nest Advisors — Business Cards</title>
<link rel="stylesheet" href="https://fonts.googleapis.com/css2?family=Cinzel:wght@400;500&family=Arimo:wght@400;700&display=swap">
<style>
  :root {
    --page-bg: #e7e4df;
    --card-grey: #8f9396;
    --card-blue: #01449a;
    --card-white: #ffffff;
    --brand-blue: #0a4ea3;
    --ink: #111111;
    --ink-soft: #1e1e1e;
    --light: #ffffff;
    --shadow: 0 6px 14px rgba(0, 0, 0, 0.35);
  }
  * { box-sizing: border-box; margin: 0; padding: 0; }
  html, body {
    width: 1200px;
    height: 1000px;
    overflow: hidden;
  }
  body {
    position: relative;
    background: var(--page-bg);
    font-family: "Arimo", Arial, sans-serif;
  }
  .card {
    position: absolute;
    width: 557px;
    height: 326px;
    border-radius: 18px;
    box-shadow: var(--shadow);
    overflow: hidden;
  }
  .card--front-grey { left: 22px; top: 150px; background: var(--card-grey); color: var(--ink); }
  .card--front-blue { left: 620px; top: 150px; background: var(--card-blue); color: var(--light); }
  .card--back { left: 321px; top: 522px; background: var(--card-white); color: var(--ink); }

  .brand-name {
    font-family: "Cinzel", Georgia, serif;
    font-weight: 500;
    letter-spacing: 0.5px;
    line-height: 1.15;
  }
  .front-brand {
    position: absolute;
    left: 0; right: 0;
    top: 118px;
    display: flex;
    align-items: center;
    justify-content: center;
    gap: 14px;
    font-size: 27px;
  }
  .card--front-grey .front-brand { color: var(--brand-blue); }
  .card--front-blue .front-brand { color: var(--light); }
  .brand-dot {
    width: 14px; height: 14px;
    border-radius: 50%;
    background: currentColor;
    flex: none;
  }
  .tagline {
    position: absolute;
    left: 0; right: 0;
    top: 280px;
    text-align: center;
    font-family: "Cinzel", Georgia, serif;
    font-size: 13.5px;
    letter-spacing: 0.2px;
  }

  .back-brand {
    position: absolute;
    left: 22px; top: 36px;
    font-size: 21px;
    color: var(--brand-blue);
    width: 250px;
  }
  .contact {
    position: absolute;
    right: 17px;
    text-align: right;
    color: var(--ink-soft);
    font-size: 13.5px;
    line-height: 18px;
  }
  .contact--person { top: 146px; }
  .contact--reach { top: 258px; }
  .person-name {
    font-weight: 700;
    font-size: 15px;
    letter-spacing: 0.3px;
    color: var(--ink);
    margin-bottom: 7px;
  }
  .sep { padding: 0 7px; }
</style>
</head>
<body>

  <section class="card card--front-grey" aria-label="Card front, grey">
    <div class="front-brand brand-name"><span class="brand-dot"></span>Harborview Nest Advisors, LLC</div>
    <p class="tagline">Turning Your Earned Income Into Retirement Income</p>
  </section>

  <section class="card card--front-blue" aria-label="Card front, blue">
    <div class="front-brand brand-name"><span class="brand-dot"></span>Harborview Nest Advisors, LLC</div>
    <p class="tagline">Turning Your Earned Income Into Retirement Income</p>
  </section>

  <section class="card card--back" aria-label="Card contact side">
    <div class="back-brand brand-name">Harborview Nest Advisors, LLC</div>

    <div class="contact contact--person">
      <p class="person-name">GREGOR PELHAM</p>
      <p>MBA, ChFC®, CLU®</p>
      <p>Financial Advisor</p>
      <p>Registered Representative</p>
    </div>

    <div class="contact contact--reach">
      <p>Email: gpelham@harborviewnest.example</p>
      <p>Phone: (555) 318-2946<span class="sep">|</span>Toll Free Fax: (800) 555-0193</p>
      <p>2187 Meadowlark Ridge Rd., Suite K418, Virginia Beach, VA 23999</p>
    </div>
  </section>

</body>
</html>
```